Kor'v Meridell Travel

We need a sleek, professional, inviting card to elicit global travel for the experienced and professional traveler. Royal blue, black and silver. (perhaps the wording could be silver with black shadow?-get creative) Maybe a watermark on the front and the full raised logo on the back.
We want a stylish and modern card, but professional.

```html
<!DOCTYPE html>
<html lang="en">
<head>
<meta charset="utf-8">
<title>Kor'v Meridell Travel – Business Card</title>
<link href="https://fonts.googleapis.com/css2?family=Open+Sans:ital,wght@0,400;0,700;0,800;1,400&display=swap" rel="stylesheet">
<style>
  :root {
    --page-bg: #2a2a2c;
    --card-bg: #1f1f20;
    --brand-blue: #27a9e1;
    --accent-green: #8cc63f;
    --text-grey: #c9c9c9;
    --muted-grey: #a8a8a8;
    --silver: #8e8e90;
  }
  * { margin: 0; padding: 0; box-sizing: border-box; }
  html, body {
    width: 1200px; height: 900px; overflow: hidden;
    background: var(--page-bg);
    font-family: "Open Sans", Arial, sans-serif;
  }
  .stage {
    width: 1200px; height: 900px;
    display: flex; flex-direction: column;
    align-items: center; justify-content: center; gap: 24px;
  }
  .card {
    width: 700px; height: 400px;
    background: var(--card-bg);
    box-shadow: 0 10px 30px rgba(0,0,0,0.55);
    position: relative;
  }
  /* Front */
  .card-front { display: flex; align-items: center; }
  .brand {
    width: 330px; padding-left: 40px;
    display: flex; align-items: center; gap: 12px;
  }
  .brand-mark { width: 14px; height: 14px; background: var(--brand-blue); flex: none; }
  .brand-name {
    color: var(--brand-blue);
    font-weight: 700; font-size: 24px; line-height: 1.2;
    letter-spacing: 0.5px; text-transform: uppercase;
  }
  .divider {
    width: 1.5px; height: 200px; background: var(--brand-blue);
    margin-right: 30px;
  }
  .contact { color: var(--text-grey); }
  .person-name {
    color: var(--brand-blue); font-weight: 800; font-size: 24px;
    text-transform: uppercase; letter-spacing: 0.5px;
  }
  .person-title { font-style: italic; font-size: 17px; color: var(--muted-grey); margin-bottom: 10px; }
  .address { font-size: 17px; line-height: 1.35; margin-bottom: 8px; }
  .contact-list { list-style: none; font-size: 17px; line-height: 1.45; }
  .contact-list li { display: flex; align-items: center; gap: 8px; }
  .contact-list svg { width: 13px; height: 13px; fill: var(--accent-green); flex: none; }
  /* Back */
  .card-back { display: flex; align-items: center; justify-content: center; }
  .back-name {
    color: var(--silver); font-weight: 700; font-size: 40px;
    text-transform: uppercase; letter-spacing: 1px;
  }
</style>
</head>
<body>
<main class="stage">
  <section class="card card-front">
    <div class="brand">
      <span class="brand-mark"></span>
      <span class="brand-name">Kor'v Meridell<br>Travel</span>
    </div>
    <div class="divider"></div>
    <div class="contact">
      <h1 class="person-name">Dalen Orrick</h1>
      <p class="person-title">President</p>
      <p class="address">4718 Corvane Harbor<br>Lysport CA 90412</p>
      <ul class="contact-list">
        <li><svg viewBox="0 0 24 24"><path d="M6.6 10.8a15 15 0 0 0 6.6 6.6l2.2-2.2a1 1 0 0 1 1-.25 11.4 11.4 0 0 0 3.6.57 1 1 0 0 1 1 1V20a1 1 0 0 1-1 1A17 17 0 0 1 3 4a1 1 0 0 1 1-1h3.5a1 1 0 0 1 1 1c0 1.25.2 2.45.57 3.57a1 1 0 0 1-.25 1z"/></svg>555-014-2287</li>
        <li><svg viewBox="0 0 24 24"><path d="M2 5h20v14H2z M2 5l10 8 10-8" stroke="#1f1f20" stroke-width="1.5"/></svg>info@korvmeridell.com</li>
        <li><svg viewBox="0 0 24 24"><circle cx="12" cy="12" r="10"/><path d="M2 12h20M12 2c3 3 3 17 0 20M12 2c-3 3-3 17 0 20" stroke="#1f1f20" stroke-width="1.5" fill="none"/></svg>www.korvmeridell.com</li>
      </ul>
    </div>
  </section>
  <section class="card card-back">
    <span class="back-name">Kor'v Meridell Travel</span>
  </section>
</main>
</body>
</html>
```